Carrying bags for customer visit

I am looking to make a carrying case that can be used to carry small presents, gifts, our brochure (20 inch X20 inch) and sometimes our samples (which are printed circuit boards that have a size of 24X15). The case should look elegant, show our company logo and our slogan "PCB is our business". You can try to download our logo from our web site www.tvolamiq.com. I want a contemporary and cool feel of the carrying case that can be any materials. I prefer to use recyclable materials that reflects our company's business philosophy of practicing sustanbility. Also I would like to add Chinese name “泓岚科技(东莞)有限公司" in the bag.

Target Market(s)

Corporate customers who will come into contact with our companies

Colors

Designer to choose colors to be used in the design.

Requirements
Must have
• It has to be attractive and people wanting to use them on a regular basis. Therefore, the logo display and our slogan should be subtle. I want the carrying bags not to be very expensive to produce.

```html
<!DOCTYPE html>
<html lang="zh">
<head>
<meta charset="utf-8">
<title>TVOLAMIQ carrying bag</title>
<link href="https://fonts.googleapis.com/css2?family=Exo+2:wght@500;700;800&family=Noto+Serif+SC:wght@400&display=swap" rel="stylesheet">
<style>
  :root {
    --teal: #0b6a66;
    --teal-side: #0a7a78;
    --yellow: #f3e000;
    --yellow-deep: #dcbf00;
    --paper: #f7f7f7;
    --ink: #222;
    --backdrop: #e4e4e4;
  }
  * { box-sizing: border-box; margin: 0; padding: 0; }
  html, body { width: 1200px; height: 900px; overflow: hidden; }
  body {
    background: var(--backdrop);
    font-family: "Exo 2", sans-serif;
    display: flex; align-items: center; justify-content: center; gap: 60px;
  }
  .bag { display: flex; height: 620px; }
  .gusset { width: 44px; background: var(--teal-side); }
  .face {
    position: relative; width: 420px; height: 620px;
    background: var(--paper); overflow: hidden;
  }
  .face svg.band { position: absolute; inset: 0; width: 100%; height: 100%; }
  .circuit-top {
    position: absolute; left: 40px; top: 0; width: 340px; height: 170px;
    background: linear-gradient(180deg, rgba(11,106,102,0.28), rgba(11,106,102,0.04));
  }
  .circuit-band {
    position: absolute; left: 0; right: 0; top: 430px; height: 44px;
    background: linear-gradient(90deg, rgba(10,122,120,0.05), rgba(10,122,120,0.3));
  }
  .brand {
    position: absolute; left: 0; right: 0; text-align: center;
    color: var(--teal); font-weight: 800; letter-spacing: 0.04em;
  }
  .slogan {
    position: absolute; left: 0; right: 0; text-align: center;
    color: var(--teal); font-weight: 700; letter-spacing: 0.55em;
  }
  .cn-name {
    position: absolute; left: 0; right: 0; text-align: center;
    font-family: "Noto Serif SC", serif; color: var(--ink);
  }
  .front .brand { top: 255px; font-size: 56px; }
  .front .slogan { top: 330px; font-size: 13px; }
  .front .cn-name { top: 370px; font-size: 22px; }
  .foot {
    position: absolute; right: 40px; bottom: 50px; text-align: right; color: #fff;
  }
  .foot .foot-brand { font-size: 26px; font-weight: 800; letter-spacing: 0.04em; }
  .foot .url { font-size: 13px; font-weight: 500; }
  .back .brand { top: 270px; font-size: 46px; }
  .back .slogan { top: 332px; font-size: 11px; }
  .back .cn-name { top: 365px; font-size: 16px; }
  .back .url {
    position: absolute; left: 0; right: 0; bottom: 50px; text-align: center;
    font-size: 11px; color: var(--ink);
  }
</style>
</head>
<body>
  <div class="bag">
    <div class="gusset"></div>
    <section class="face front">
      <svg class="band" viewBox="0 0 420 620" preserveAspectRatio="none">
        <polygon points="0,620 420,460 420,620" fill="var(--yellow)"/>
      </svg>
      <div class="circuit-top" role="img" aria-label="Circuit board trace pattern hanging from the top edge"></div>
      <div class="brand">TVOLAMIQ</div>
      <div class="slogan">IS OUR BUSINESS</div>
      <div class="cn-name">泓岚科技（东莞）有限公司</div>
      <div class="foot">
        <div class="foot-brand">TVOLAMIQ</div>
        <div class="url">www.tvolamiq.com</div>
      </div>
    </section>
  </div>

  <div class="bag">
    <section class="face back">
      <svg class="band" viewBox="0 0 420 620" preserveAspectRatio="none">
        <polygon points="0,60 420,0 420,40 0,210" fill="var(--yellow-deep)"/>
      </svg>
      <div class="brand">TVOLAMIQ</div>
      <div class="slogan">IS OUR BUSINESS</div>
      <div class="cn-name">泓岚科技（东莞）有限公司</div>
      <div class="circuit-band" role="img" aria-label="Horizontal circuit board trace lines"></div>
      <div class="url">www.tvolamiq.com</div>
    </section>
    <div class="gusset"></div>
  </div>
</body>
</html>
```